Web design required

1-We need a web design for existing company based in New Zealand
2-We build residential house and light commercial
3-We has in-house designer which allow us can provide interior design
4-We modeling project before site construction, which enable both client and construction team to visually analysis whole project,

Target Market(s)

middle class residential house market
Ref: http://www.parvellbuilders.co.nz/

Industry/Entity Type

Construction Company

Number of Pages Required

1 page

Font styles to use
Sans Serif
Other font styles liked:
• Such as : Central Gothic or similar which has more design taste

Colors

Designer to choose colors to be used in the design.

Requirements
Must have
• Front sheet, contact information, sample project

```html
<!DOCTYPE html>
<html lang="en">
<head>
<meta charset="utf-8">
<title>Kowhai Homes</title>
<link rel="stylesheet" href="https://fonts.googleapis.com/css2?family=Didact+Gothic&family=Montserrat:wght@500;600;700&display=swap">
<style>
:root{
  --blue:#1b5aa3;
  --navy:#184f8e;
  --ink:#1d1d1d;
  --grey:#666;
  --light:#f2f2f2;
  --line:#dcdcdc;
  --white:#fff;
}
*{box-sizing:border-box;margin:0;padding:0}
html,body{width:1200px;height:2601px;overflow:hidden;background:var(--white)}
body{position:relative;font-family:"Didact Gothic",sans-serif;color:var(--ink)}
.abs{position:absolute}

/* nav */
.nav{top:0;left:0;width:1200px;height:69px;background:var(--white)}
.nav a{position:absolute;top:24px;font-family:"Montserrat",sans-serif;font-size:13px;font-weight:500;color:#222;text-decoration:none;letter-spacing:.5px}
.nav a.active{color:var(--blue)}
.nav .marker{position:absolute;left:213px;top:45px;width:2px;height:24px;background:var(--blue)}
.brand{position:absolute;left:478px;top:15px;display:flex;align-items:center;gap:10px}
.brand .dot{width:36px;height:36px;background:var(--navy);display:block}
.brand span{font-family:"Montserrat",sans-serif;font-weight:500;font-size:21px;color:#333;letter-spacing:.3px;white-space:nowrap}

/* hero */
.hero{top:69px;left:0;width:1200px;height:573px;background:linear-gradient(180deg,#5a4a55 0%,#3a3538 35%,#2b2a2a 70%,#3b3d3b 100%)}
.hero-frame{left:200px;top:118px;width:232px;height:330px;border:1px solid rgba(255,255,255,.7)}
.num{font-family:"Montserrat",sans-serif;font-weight:700;font-size:36px}
.kicker{font-size:20px}
.hero .num{left:233px;top:194px;color:#fff}
.hero .kicker{left:291px;top:236px;color:#ddd}
.hero h1{left:291px;top:272px;font-family:"Montserrat",sans-serif;font-weight:700;font-size:58px;line-height:74px;color:#fff;white-space:nowrap}
.hero .arrow{top:270px}
.dots{left:200px;top:485px;display:flex;gap:3px}
.dots i{width:9px;height:9px;border:1px solid #ccc;display:block}
.dots i.on{background:var(--blue);border-color:var(--blue)}

/* section titles */
.title-block{text-align:right;right:198px}
.title-block .num{color:#111;font-size:38px}
.title-block .kicker{color:#888;margin-top:6px}
.title-block h2{font-family:"Montserrat",sans-serif;font-weight:700;font-size:32px;color:#111;margin-top:2px}
h2 em{font-style:normal;color:var(--blue)}
.lede{font-size:14px;line-height:26px;color:#555;letter-spacing:.8px}

/* services */
.services{top:642px;left:0;width:1200px;height:445px}
.card{top:116px;width:160px;height:253px;background:#fff;box-shadow:0 2px 8px rgba(0,0,0,.18);text-align:center}
.card .tab{position:absolute;left:50px;top:-18px;width:60px;height:44px;background:#fff}
.card svg{position:absolute;left:64px;top:-14px}
.card h3{margin-top:72px;font-family:"Montserrat",sans-serif;font-size:13px;font-weight:600;line-height:20px;color:#111}
.card .rule{width:38px;height:3px;background:var(--blue);margin:10px auto 12px}
.card p{font-size:12.5px;line-height:19px;color:#333;padding:0 14px;letter-spacing:.4px}
.btn{display:inline-block;background:var(--navy);color:#fff;font-family:"Montserrat",sans-serif;font-weight:600;font-size:9px;letter-spacing:.5px;position:relative}
.card .btn{margin-top:14px;padding:8px 10px}
.btn::after{content:"";position:absolute;right:0;bottom:0;border-left:6px solid transparent;border-bottom:6px solid #fff}

/* about */
.about{top:1087px;left:0;width:1200px;height:401px;background:linear-gradient(100deg,#3a3a3a 0%,#4d4c4a 45%,#5a5856 70%,#3e3d3c 100%)}
.about .num{left:222px;top:58px;color:#fff}
.about .kicker{left:222px;top:106px;color:#ddd}
.about h2{left:222px;top:134px;font-family:"Montserrat",sans-serif;font-weight:700;font-size:32px;color:#fff}
.about p{left:222px;top:192px;width:765px;font-size:13.5px;line-height:23px;color:#fff;letter-spacing:.6px}
.ghost{border:1px solid #fff;color:#fff;font-family:"Montserrat",sans-serif;font-size:12px;font-weight:600;text-align:center;line-height:36px}
.about .ghost{left:220px;top:278px;width:125px;height:38px}

/* projects */
.projects{top:1488px;left:0;width:1200px;height:575px}
.photo{position:absolute}
.proj-name{font-family:"Montserrat",sans-serif;font-weight:600;font-size:15px;color:#111}
.proj-date{font-size:13px;color:#444}
.proj-line{height:2px;background:var(--blue)}
.projects .btn{left:796px;top:274px;width:175px;height:41px;line-height:41px;text-align:center;font-size:12px}

/* contact */
.contact{top:2063px;left:0;width:1200px;height:406px}
.contact-photo{left:0;top:0;width:600px;height:406px;background:linear-gradient(180deg,#3b4147 0%,#2c2f31 55%,#3a3c38 100%)}
.map{left:600px;top:0;width:600px;height:406px;background:linear-gradient(135deg,#d9d9d9,#c8c8c8 50%,#d4d4d4)}
.contact .num{left:217px;top:36px;color:#fff}
.contact .kicker{left:217px;top:86px;color:#ddd}
.contact h2{left:217px;top:112px;font-family:"Montserrat",sans-serif;font-weight:700;font-size:32px;color:#fff}
.field{position:absolute;border-bottom:1px solid rgba(255,255,255,.8);color:#fff;font-family:"Montserrat",sans-serif;font-size:9px;font-weight:600;letter-spacing:.5px;padding-bottom:8px}
.contact .ghost{left:220px;top:321px;width:99px;height:30px;line-height:28px;font-size:10px}

/* footer */
.footer{top:2469px;left:0;width:1200px;height:132px;background:#fff;font-size:12.5px;color:#222;line-height:24px}
.footer h4{font-family:"Montserrat",sans-serif;font-weight:700;font-size:13px;letter-spacing:.5px}
.social{display:flex;gap:8px;margin-top:12px}
.social i{display:block;width:19px;height:19px}
</style>
</head>
<body>

<nav class="abs nav">
  <a class="active" style="left:200px">HOME</a>
  <a style="left:272px">SERVICES</a>
  <a style="left:369px">ABOUT US</a>
  <div class="brand"><i class="dot"></i><span>KOWHAI HOMES</span></div>
  <a style="left:752px">PROJECTS</a>
  <a style="left:855px">CONTACT</a>
  <a style="left:950px">SEARCH</a>
  <span class="marker"></span>
</nav>

<section class="abs hero" role="img" aria-label="Photograph of a large stone two-storey home at dusk with lit windows">
  <div class="abs hero-frame"></div>
  <div class="abs num">01.</div>
  <div class="abs kicker">Kowhai Homes</div>
  <h1 class="abs">WELCOME<br>TO KOWHAI HOMES</h1>
  <svg class="abs arrow" style="left:85px" width="20" height="34" viewBox="0 0 20 34"><path d="M17 2 3 17l14 15" fill="none" stroke="#fff" stroke-width="2.5"/></svg>
  <svg class="abs arrow" style="left:1093px" width="20" height="34" viewBox="0 0 20 34"><path d="M3 2l14 15L3 32" fill="none" stroke="#fff" stroke-width="2.5"/></svg>
  <div class="abs dots"><i class="on"></i><i></i><i></i></div>
</section>

<section class="abs services">
  <div class="abs title-block" style="top:10px">
    <div class="num">02.</div>
    <div class="kicker">Kowhai Homes</div>
    <h2>OUR <em>SERVICES</em></h2>
  </div>
  <p class="abs lede" style="right:224px;top:146px;width:230px;text-align:right">Kowhai Homes is dedicated to creating and renovating beauti-ful and unusual buildings.Kowhai Homes works..</p>

  <div class="abs card" style="left:200px">
    <div class="tab"></div>
    <svg width="32" height="34" viewBox="0 0 32 34" fill="none" stroke="#1b5aa3" stroke-width="1.8"><path d="M8 12a8 8 0 0 1 16 0z"/><path d="M5 12h22"/><circle cx="16" cy="17" r="4"/><path d="M4 32v-5a6 6 0 0 1 6-6h12a6 6 0 0 1 6 6v5z"/></svg>
    <h3>Preconstruction<br>Planning</h3><div class="rule"></div>
    <p>Lorem Ipsum is simply dummy text of the printing industry.</p>
    <span class="btn">LEARN MORE</span>
  </div>
  <div class="abs card" style="left:373px">
    <div class="tab"></div>
    <svg width="32" height="34" viewBox="0 0 32 34" fill="none" stroke="#1b5aa3" stroke-width="1.8"><rect x="6" y="2" width="14" height="30"/><rect x="20" y="12" width="8" height="20"/><path d="M10 7h2M14 7h2M10 12h2M14 12h2M10 17h2M14 17h2M10 22h2M14 22h2M23 17h2M23 22h2M2 32h28"/></svg>
    <h3>Preconstruction<br>Planning</h3><div class="rule"></div>
    <p>Lorem Ipsum is simply dummy text of the printing industry.</p>
    <span class="btn">LEARN MORE</span>
  </div>
  <div class="abs card" style="left:546px">
    <div class="tab"></div>
    <svg width="34" height="34" viewBox="0 0 34 34" fill="none" stroke="#1b5aa3" stroke-width="1.8"><circle cx="17" cy="17" r="6"/><circle cx="17" cy="4" r="3"/><circle cx="17" cy="30" r="3"/><circle cx="4" cy="17" r="3"/><circle cx="30" cy="17" r="3"/><path d="M17 7v4M17 23v4M7 17h4M23 17h4"/></svg>
    <h3>Preconstruction<br>Planning</h3><div class="rule"></div>
    <p>Lorem Ipsum is simply dummy text of the printing industry.</p>
    <span class="btn">LEARN MORE</span>
  </div>
</section>

<section class="abs about" role="img" aria-label="Photograph of a bright modern living room with sofa, floor lamp and artwork">
  <div class="abs num">03.</div>
  <div class="abs kicker">Kowhai Homes</div>
  <h2 class="abs">ABOUT <em>US</em></h2>
  <p class="abs">Kowhai Homes is dedicated to creating and renovating beautiful and unusual buildings.Kowhai Homes works with you to take dream houses off the blueprints and into reality. We have the knowledge and expertise to customise homes to suit you from unusual materials and designs to environmentally sensitive locations.</p>
  <div class="abs ghost">READ MORE</div>
</section>

<section class="abs projects">
  <div class="abs title-block" style="top:14px">
    <div class="num">04.</div>
    <div class="kicker">Kowhai Homes</div>
    <h2>OUR <em>PROJECTS</em></h2>
  </div>
  <p class="abs lede" style="right:224px;top:146px;width:230px;text-align:right">Kowhai Homes is dedicated to creating and renovating beautiful and unusual buildings.Kowhai Homes works..</p>
  <div class="abs btn">VIEW MORE PROJECTS</div>

  <div class="photo" style="left:200px;top:100px;width:181px;height:210px;background:linear-gradient(135deg,#e8e4de,#8a7560 60%,#3e3a36)" role="img" aria-label="Interior photograph of a timber staircase with glass balustrade"></div>
  <div class="abs proj-name" style="left:399px;top:108px">Tawhiti Project - Interior</div>
  <div class="abs proj-line" style="left:381px;top:142px;width:50px"></div>
  <div class="abs proj-date" style="left:440px;top:133px">6 Nov-2017</div>
  <div class="photo" style="left:400px;top:168px;width:294px;height:142px;background:linear-gradient(180deg,#2c3a4e,#4a5868 60%,#333)" role="img" aria-label="Photograph of a modern white home at dusk">
    <div class="abs" style="left:8px;top:8px;right:8px;bottom:8px;border:1px solid rgba(255,255,255,.7)"></div>
    <svg class="abs" style="left:137px;top:61px" width="20" height="20" viewBox="0 0 20 20"><path d="M10 2v16M2 10h16" stroke="#fff" stroke-width="3"/></svg>
  </div>

  <div class="photo" style="left:200px;top:327px;width:294px;height:174px;background:linear-gradient(180deg,#cfd2d4,#3a3a3a 50%,#7a6a55)" role="img" aria-label="Photograph of a dark clad modern home with glass balcony"></div>
  <div class="abs proj-name" style="left:508px;top:332px">Miro Rd Project</div>
  <div class="abs proj-line" style="left:480px;top:364px;width:60px"></div>
  <div class="abs proj-date" style="left:551px;top:355px">6 Nov-2017</div>
  <div class="photo" style="left:510px;top:379px;width:184px;height:122px;background:linear-gradient(180deg,#9ec3e6,#d8dde0 55%,#7f8a77)" role="img" aria-label="Photograph of a house under construction with scaffolding"></div>
</section>

<section class="abs contact">
  <div class="abs contact-photo" role="img" aria-label="Photograph of a modern home with garage at dusk"></div>
  <div class="abs map" role="img" aria-label="Street map of the office location with a red pin">
    <svg class="abs" style="left:358px;top:148px" width="16" height="24" viewBox="0 0 16 24"><path d="M8 23S1 13 1 8a7 7 0 0 1 14 0c0 5-7 15-7 15z" fill="#d93025"/><circle cx="8" cy="8" r="2.5" fill="#8b1a14"/></svg>
    <div class="abs" style="right:8px;bottom:22px;width:20px;height:40px;background:#fff;box-shadow:0 1px 3px rgba(0,0,0,.3);font:600 14px/20px Montserrat,sans-serif;text-align:center;color:#444">+<br>-</div>
  </div>
  <div class="abs num">05.</div>
  <div class="abs kicker">Kowhai Homes</div>
  <h2 class="abs">CONTACT <em>US</em></h2>
  <div class="field" style="left:217px;top:186px;width:170px">YOUR NAME *</div>
  <div class="field" style="left:404px;top:186px;width:137px">YOUR PHONE *</div>
  <div class="field" style="left:217px;top:222px;width:324px">SUBJECT *</div>
  <div class="field" style="left:217px;top:264px;width:324px;padding-bottom:22px">MESSAGE *</div>
  <div class="abs ghost"><svg width="11" height="10" viewBox="0 0 11 10" style="margin-right:6px;vertical-align:-1px"><path d="M0 4 11 0 7 10 5 6z" fill="#fff"/></svg>SUBMIT</div>
</section>

<footer class="abs footer">
  <div class="abs" style="left:200px;top:24px">© kowhai homes 2017<br>All Rights Reserved
    <div class="social"><i style="background:#3b5998"></i><i style="background:#cb2027"></i><i style="background:#1da1f2"></i><i style="background:#dd4b39"></i></div>
  </div>
  <div class="abs" style="left:418px;top:24px">Site Map<br>Term &amp; Conditions<br>Privacy Policy<br>Help</div>
  <div class="abs" style="left:609px;top:24px">
    <h4>KEEP IN TOUCH</h4>
    <div style="margin-top:14px"><svg width="10" height="16" viewBox="0 0 10 16" style="margin-right:10px;vertical-align:-3px"><rect x="1" y="1" width="8" height="14" rx="1.5" fill="none" stroke="#1d3f72" stroke-width="1.6"/></svg>0064 9 000 4821</div>
    <div style="margin-top:6px"><svg width="14" height="10" viewBox="0 0 14 10" style="margin-right:8px"><rect x="1" y="1" width="12" height="8" fill="none" stroke="#1d3f72" stroke-width="1.4"/><path d="M1 1l6 5 6-5" fill="none" stroke="#1d3f72" stroke-width="1.4"/></svg>info@kowhaihomes.example</div>
  </div>
  <div class="abs" style="left:813px;top:24px">
    <h4>ADDRESS</h4>
    <div style="margin-top:14px;display:flex;gap:12px;width:190px"><svg width="16" height="14" viewBox="0 0 16 14" style="flex:none;margin-top:4px"><path d="M8 1 1 7h2v6h4V9h2v4h4V7h2z" fill="#1d3f72"/></svg><span>18 Tawa Crescent, Kereru Bay Northdale..</span></div>
  </div>
</footer>

</body>
</html>
```